Corporate Business Card

Very professional, Modern, Not to busy, include phone address email, website
(253) 617-4930, 18761 52nd Avenue S, Kent, WA 98047, martin@plumlinegroup.com, varkoworks.com

Target Market(s)

Manufacturing

Industry/Entity Type

Aero, machining, manufacturing, Off road racing

Contact Information for Business Card

Phone, address email, website

```html
<!DOCTYPE html>
<html lang="en">
<head>
<meta charset="utf-8">
<title>Varko Works Business Card</title>
<link rel="stylesheet" href="https://fonts.googleapis.com/css2?family=Open+Sans:wght@400;600;700;800&display=swap">
<style>
  :root {
    --backdrop: #232323;
    --navy: #17336b;
    --red: #d42630;
    --white: #ffffff;
    --ink: #4a4a4a;
    --shadow: rgba(0, 0, 0, 0.45);
  }
  * { margin: 0; padding: 0; box-sizing: border-box; }
  html, body {
    width: 1200px;
    height: 786px;
    overflow: hidden;
    background: var(--backdrop);
    font-family: "Open Sans", sans-serif;
  }
  .stage {
    position: relative;
    width: 1200px;
    height: 786px;
  }
  .card {
    position: absolute;
    width: 520px;
    height: 297px;
    border-radius: 22px;
    box-shadow: 0 12px 30px var(--shadow);
  }
  .card-front {
    left: 50px;
    top: 245px;
    background: var(--navy);
    display: flex;
    align-items: center;
    justify-content: center;
    gap: 14px;
  }
  .brand-mark {
    width: 26px;
    height: 26px;
    background: var(--red);
  }
  .brand-name {
    color: var(--white);
    font-weight: 800;
    font-size: 44px;
    letter-spacing: 2px;
  }
  .card-back {
    left: 630px;
    top: 245px;
    background: var(--white);
  }
  .identity {
    position: absolute;
    right: 262px;
    top: 118px;
    text-align: right;
  }
  .person-name {
    color: var(--navy);
    font-weight: 800;
    font-size: 27px;
    letter-spacing: 0.3px;
    line-height: 1.1;
  }
  .person-role {
    color: var(--red);
    font-size: 16px;
    line-height: 1.3;
  }
  .divider {
    position: absolute;
    left: 272px;
    top: 92px;
    width: 1.5px;
    height: 118px;
    background: var(--navy);
  }
  .contact-list {
    position: absolute;
    left: 288px;
    top: 96px;
    list-style: none;
  }
  .contact-item {
    display: flex;
    align-items: flex-start;
    gap: 8px;
    color: var(--ink);
    font-size: 12.5px;
    line-height: 18px;
  }
  .contact-icon {
    width: 11px;
    height: 11px;
    margin-top: 4px;
    flex: none;
    fill: var(--navy);
  }
</style>
</head>
<body>
<main class="stage">
  <section class="card card-front" aria-label="Card front">
    <span class="brand-mark"></span>
    <span class="brand-name">VARKO WORKS</span>
  </section>

  <section class="card card-back" aria-label="Card back">
    <div class="identity">
      <p class="person-name">DANIEL BROOKS</p>
      <p class="person-role">Managing Director</p>
    </div>
    <div class="divider"></div>
    <ul class="contact-list">
      <li class="contact-item">
        <svg class="contact-icon" viewBox="0 0 12 12"><path d="M6 0a4 4 0 0 0-4 4c0 3 4 8 4 8s4-5 4-8a4 4 0 0 0-4-4zm0 5.6A1.6 1.6 0 1 1 6 2.4a1.6 1.6 0 0 1 0 3.2z"/></svg>
        <span>18761 52nd Avenue S<br>Kent, WA 98047</span>
      </li>
      <li class="contact-item">
        <svg class="contact-icon" viewBox="0 0 12 12"><path d="M2.4 0.6l2 2.2-1 1.4c.7 1.6 2 2.9 3.6 3.6l1.4-1 2.2 2-1 2.2C5 10.8 1.2 7 .6 1.6z"/></svg>
        <span>(253) 617-4930</span>
      </li>
      <li class="contact-item">
        <svg class="contact-icon" viewBox="0 0 12 12"><path d="M0 2h12v8H0zM.8 2.8 6 6.6l5.2-3.8v-.1H.8z"/></svg>
        <span>martin@plumlinegroup.com</span>
      </li>
      <li class="contact-item">
        <svg class="contact-icon" viewBox="0 0 12 12"><path d="M6 0a6 6 0 1 0 0 12A6 6 0 0 0 6 0zm0 1.2c.7 0 1.5 1.6 1.7 3.8H4.3C4.5 2.8 5.3 1.2 6 1.2zM4.3 7h3.4C7.5 9.2 6.7 10.8 6 10.8S4.5 9.2 4.3 7z"/></svg>
        <span>www.varkoworks.com</span>
      </li>
    </ul>
  </section>
</main>
</body>
</html>
```